Website Design for a Luxury Wedding & Events Company

We are launching a British luxury wedding & event planning consultancy business providing bespoke, elegant and first-class service to our discerning clients in the UK and abroad. We specialize in Weddings (which will have it's on page) however we also provide service for other occasion which will be included in a single page 'Events'.

We require a company website design befitting of our luxury brand. Once designed we will post another job to code the website so that it can be hosted by HostPlume.com.

The website has to set the tone for our business and type of premium service we provide. Our website design has to be BESPOKE and have a luxury and elegant look and feel about it.

PLEASE REFER TO THE IMAGES ATTACHED TO GET AN UNDERSTANDING OF THE DESIGN CONCEPT WE WANT. ALL DESIGNS SUBMITTED MUST FOLLOW THE CONCEPT SPECIFIED!!!

We appreciate that the current budget will not permit for the design of all pages referenced above, so we are happy to have designs for up to 3 pages initially; Landing page (we have attached an examples of what we want), 'Home' page (an example is also attached) and 'About' us page. When we are happy with a particular design we can add payment for remainder of the pages required.

The final website design will have the following pages:
1a) URL Landing Page (details below)
1b) Home
2) About
3) Luxury Weddings
4) Services (this can either be a separate tab or linked to 'Luxury Weddings' - however it does need to be a separate page)
subheadings are:
> Comprehensive Wedding Planning Service
> Wedding Day Coordination Service
> Consultancy Service
5) Events
6) Gallery
7) Testimonials
8) Contact

We have a concept of the website is as follows:
URL Landing Page:
Option 1: This should just be simple but makes an immediate statement.
We have attached an image of how this could potentially look. The logo featured in the photo example needs to be replaced with our logo (reference site: http://tesslovank.com/).

Option 2: Alternatively this could be an actually door in the middle of the page - Imagine the big black gloss door at Number 14 Corwell Terrace (London Prime Minister's home).

By clicking the door knocker on either options , the 'Home Page' will be opened.

Our tag line should also be tastefully integrated:
'Exclusive Events, Masterfully Produced, Distinctively Designed'

The 'HOME PAGE' - should look like a luxury boutique office or reception lounge (luxury table, luxury head chair and luxury 2 client chairs; elegant chandelier, beautiful flowers on the table, 2 flutes of champagne on the table; and filing cabinets with drawers that are labelled with different website pages, e.g. 'about us', 'services', 'gallery', etc. By clicking on the drawers the details behind that page will open up in a separate tab/page.)

Our tag line should be on the Home Page also.

The overall concept and look and feel of website is all about taking people on a journey and giving them a glimpse of the luxury service that awaits them.

Colours: We want the general look and feel of the website to be WHITE, or OFF-WHITE with soft hints of gold to match the logo (tab/page headings could be gold). The only dark page should be the URL Landing page (ref to website images attached).

The website and images need to be compatible with mobile devices, smartphones, Tabros, etc. In terms of fit to screen, resolution etc...

We require links to our Pagewall, Quillet, Snapvuely and Boardlyne Pages (links to be provided later)

This is the rough concept and looking for designers to try to elevate this vision. :-) We are open for designers to interpret this concept in their own way.

Website wording/content is all ready to go...

We have attached our logo, and some imagery to help...

Target Market(s)

Luxury Wedding & Events Market

Industry/Entity Type

Wedding Planner

Number of Pages Required

3 page

Font styles to use
Sans Serif

Colors
ffffff

Requirements
Must have
• Tag Line:
• 'Exquisite Events, Masterfully Produced, Distinctively Designed'

```html
<!DOCTYPE html>
<html lang="en">
<head>
<meta charset="utf-8">
<title>Elise Marlow – Luxury Wedding &amp; Event Consultants</title>
<link href="https://fonts.googleapis.com/css2?family=Raleway:wght@400;500;600&family=Playball&display=swap" rel="stylesheet">
<style>
:root{
  --black:#141414;
  --gold:#b08a1f;
  --gold-dark:#8c6c14;
  --gold-mid:#c9a13a;
  --gold-light:#e3c677;
  --white:#ffffff;
  --ink:#333333;
  --muted:#555555;
  --footer:#474747;
  --quote:#5b5b5b;
}
*{margin:0;padding:0;box-sizing:border-box}
html,body{width:1200px;height:2965px;overflow:hidden;background:var(--white)}
body{font-family:"Raleway",sans-serif;color:var(--ink);position:relative}
.abs{position:absolute}
.script{font-family:"Playball",cursive;font-weight:400}

/* header */
.site-header{left:0;top:0;width:1200px;height:166px;background:var(--black)}
.contact-lines{left:102px;top:38px;color:var(--white);font-size:16px;line-height:26px}
.brand{left:450px;top:8px;width:300px;text-align:center;color:var(--gold-light)}
.brand-mark{width:64px;height:64px;border:2px solid var(--gold-light);border-radius:50%;margin:0 auto 8px}
.brand-name{font-size:19px;letter-spacing:3px;text-transform:uppercase;font-weight:500}
.social{display:flex;gap:22px}
.social span{width:32px;height:32px;border:1.5px solid var(--white);border-radius:50%;display:block}
.header-social{left:910px;top:48px}

.main-nav{left:148px;top:134px;width:904px;height:36px;background:var(--gold);display:flex;justify-content:space-around;align-items:center;padding:0 30px;z-index:2}
.main-nav a{color:var(--white);text-decoration:none;font-size:14px}
.main-nav a::before{content:"• "}
.nav-tail{top:134px;width:0;height:0;border-top:18px solid var(--gold-dark);border-bottom:18px solid var(--gold-dark);z-index:1}

/* hero */
.hero{left:0;top:166px;width:1200px;height:530px;
  background:
    linear-gradient(180deg,rgba(255,255,255,0) 0%,rgba(255,255,255,.35) 70%,rgba(240,226,190,.6) 100%),
    linear-gradient(90deg,#dcb65a 0%,#eed79c 16%,#f8f0dc 34%,#fdfaf2 50%,#f8f0dc 66%,#eed79c 84%,#d9b253 100%)}
.hero-arrow{left:16px;top:420px;width:30px;height:30px;border-radius:50%;background:rgba(255,255,255,.6)}
.hero-arrow::after{content:"";position:absolute;left:12px;top:10px;width:8px;height:8px;border-left:2px solid #888;border-bottom:2px solid #888;transform:rotate(45deg)}
.tagline{left:300px;top:570px;width:600px;text-align:center;color:var(--gold);font-size:29px;line-height:46px}

/* section bands */
.band-title{left:0;width:1200px;background:var(--gold);color:var(--white);text-align:center;font-size:36px}
.about-title{top:696px;height:59px;line-height:59px}
.about-body{left:0;top:755px;width:1200px;height:285px;background:var(--gold-light);text-align:center;color:var(--white);font-size:13px;line-height:21px;padding:38px 150px 0}
.about-body p+p{margin-top:18px}
.btn{display:inline-block;margin-top:22px;background:var(--white);color:var(--gold);font-size:14px;font-weight:600;padding:10px 20px;text-transform:uppercase;box-shadow:0 2px 4px rgba(0,0,0,.15)}

.section-heading{left:0;width:1200px;text-align:center;color:var(--gold-mid);font-size:38px}
.heading-rule{left:556px;width:88px;height:2px;background:var(--gold-mid)}

/* services */
.service{width:300px;text-align:center}
.service-icon{width:106px;height:106px;border-radius:50%;background:var(--gold);margin:0 auto;display:flex;align-items:center;justify-content:center;box-shadow:0 0 0 4px #fff inset,0 0 0 6px var(--gold) inset}
.service h3{font-size:16px;font-weight:500;line-height:26px;margin-top:30px;color:#222}
.service p{font-size:12.5px;line-height:19px;color:var(--muted);margin:22px auto 0;width:260px}

/* events */
.events-title{top:1453px;height:55px;line-height:55px;font-size:32px}
.event{width:300px;height:206px}
.event-text{text-align:center;padding-top:32px;background:var(--white)}
.event-text.featured{background:var(--gold-light);color:var(--white)}
.event-text h4{font-size:19px;font-weight:500;margin-bottom:10px}
.event-text .line{font-size:12.5px;line-height:25px;display:flex;justify-content:center;align-items:center;gap:6px}
.event-text svg{flex:none}
.photo{display:block}

/* gallery */
.gallery-item{display:block}

/* testimonial */
.quote-box{left:99px;top:2600px;width:1002px;height:95px;background:var(--quote);z-index:2}
.avatar{left:66px;top:16px;width:62px;height:62px;border-radius:50%;border:3px solid #ddd;background:linear-gradient(#d9b48c,#a8826a)}
.quote-text{left:198px;top:22px;width:620px;color:#ddd;font-size:12.5px;line-height:22px}
.quote-name{right:95px;top:64px;color:#eee;font-size:12px}
.quote-nav{right:62px;top:6px;color:#fff;font-size:22px;letter-spacing:12px}

/* footer */
.site-footer{left:0;top:2659px;width:1200px;height:257px;background:var(--footer)}
.footer-heading{color:var(--white);font-size:22px;text-align:center}
.footer-rule{height:1px;background:#aaa;width:60px;margin:12px auto 0}
.footer-contact{color:var(--white);font-size:16px;line-height:24px;text-align:center}
.footer-brand{left:450px;top:2718px;width:300px;text-align:center;color:var(--white)}
.footer-brand .brand-mark{border-color:var(--white);width:84px;height:84px}
.bottom-bar{left:0;top:2916px;width:1200px;height:49px;background:var(--gold);color:var(--white);font-size:12px;text-align:center;line-height:49px}
</style>
</head>
<body>

<header class="abs site-header">
  <div class="abs contact-lines">info@elisemarlow.com<br>www.weddingsbyelisemarlow.com</div>
  <div class="abs brand"><div class="brand-mark"></div><div class="brand-name">Elise Marlow</div></div>
  <div class="abs social header-social" aria-label="Social links"><span aria-label="Pagewall"></span><span aria-label="Quillet"></span><span aria-label="Boardlyne"></span><span aria-label="Snapvuely"></span></div>
</header>
<div class="abs nav-tail" style="left:134px;border-left:14px solid transparent"></div>
<div class="abs nav-tail" style="left:1052px;border-right:14px solid transparent"></div>
<nav class="abs main-nav">
  <a href="#">Home</a><a href="#">About</a><a href="#">Luxury Weddings</a><a href="#">Services</a><a href="#">Events</a><a href="#">Gallery</a><a href="#">Testimonials</a><a href="#">Contact</a>
</nav>

<section class="abs hero" role="img" aria-label="Photo: bright domed hall with white columns, marble walls and a crystal chandelier"></section>
<div class="abs hero-arrow"></div>
<p class="abs tagline script">Exclusive Events, Masterfully Produced,<br>Distinctively Designed</p>

<h2 class="abs band-title about-title script">About Us</h2>
<section class="abs about-body">
  <p>Elise Marlow is a British luxury wedding and event planning consultancy providing bespoke, elegant and first-class service to our discerning clients in the UK and abroad. Our specialist team of event planning consultants will help elevate your vision and create impeccable designs for life's most important occasions with refinement and tasteful restraint. For us merely satisfying expectations is not enough, we aim to always surpass them.</p>
  <p>We possess an extraordinary commitment to excellence and attention to detail. Whether you are planning a grand or intimate event, we will listen to your requirements and work with you to create a completely personalised and unforgettable occasion.</p>
  <span class="btn">Contact Us</span>
</section>

<h2 class="abs section-heading script" style="top:1070px">Our Services</h2>
<div class="abs heading-rule" style="top:1132px"></div>

<div class="abs service" style="left:77px;top:1173px">
  <div class="service-icon"><svg width="50" height="40" viewBox="0 0 50 40"><circle cx="18" cy="22" r="11" fill="none" stroke="#fff" stroke-width="3"/><circle cx="32" cy="22" r="11" fill="none" stroke="#fff" stroke-width="3"/></svg></div>
  <h3>Comprehensive Wedding<br>Planning Service</h3>
  <p>By starting with an initial concept such as a colour, a pattern or an era, we can help identify a focus...</p>
</div>
<div class="abs service" style="left:451px;top:1173px">
  <div class="service-icon"><svg width="40" height="46" viewBox="0 0 40 46"><rect x="8" y="4" width="24" height="36" rx="3" fill="none" stroke="#fff" stroke-width="3"/><path d="M14 14h12M14 21h12M14 28h8" stroke="#fff" stroke-width="2.5"/></svg></div>
  <h3>Wedding Day Coordination<br>Service</h3>
  <p>During an initial in-person consultation we will ascertain the progress made to-date and offer suggestions...</p>
</div>
<div class="abs service" style="left:827px;top:1173px">
  <div class="service-icon"><svg width="46" height="40" viewBox="0 0 46 40"><path d="M4 14 L23 4 L42 14 V36 H4 Z" fill="#fff"/><path d="M4 14 L23 26 L42 14" fill="none" stroke="var(--gold)" stroke-width="2.5"/></svg></div>
  <h3>Our Wedding Consultancy<br>Service</h3>
  <p>Our one-to-one consultancy service is aimed at those who want to plan much of their event themselves, selection.</p>
</div>

<h2 class="abs band-title events-title script">Other Special Events</h2>

<svg width="0" height="0" style="position:absolute">
  <defs>
    <symbol id="pin" viewBox="0 0 12 14"><path d="M6 0a5 5 0 0 0-5 5c0 4 5 9 5 9s5-5 5-9a5 5 0 0 0-5-5z" fill="currentColor"/><circle cx="6" cy="5" r="2" fill="#fff"/></symbol>
    <symbol id="cal" viewBox="0 0 12 12"><rect x="1" y="2" width="10" height="9" fill="none" stroke="currentColor" stroke-width="1.5"/><path d="M1 5h10" stroke="currentColor" stroke-width="1.5"/></symbol>
    <symbol id="clock" viewBox="0 0 12 12"><circle cx="6" cy="6" r="5" fill="none" stroke="currentColor" stroke-width="1.5"/><path d="M6 3v3h2" stroke="currentColor" stroke-width="1.3" fill="none"/></symbol>
  </defs>
</svg>

<div class="abs event event-text" style="left:0;top:1512px">
  <h4>Bachelorette Party</h4>
  <div class="line"><svg width="11" height="13" style="color:var(--gold)"><use href="#pin"/></svg>St Aldwyn Chapel</div>
  <div class="line">41-43 Harlow Row Fenbury, NY 11290</div>
  <div class="line"><svg width="11" height="11" style="color:var(--gold)"><use href="#cal"/></svg>September 20, 2015</div>
  <div class="line"><svg width="11" height="11" style="color:var(--gold)"><use href="#clock"/></svg>8 PM - 11PM</div>
</div>
<div class="abs event photo" style="left:300px;top:1512px;background:linear-gradient(135deg,#e8c9e0,#6e3a66 60%,#2a2230)" role="img" aria-label="Photo: purple lounge with dark dining table"></div>
<div class="abs event event-text" style="left:600px;top:1512px">
  <h4>Wedding Ceremony</h4>
  <div class="line"><svg width="11" height="13" style="color:var(--gold)"><use href="#pin"/></svg>St Aldwyn Chapel</div>
  <div class="line">41-43 Harlow Row Fenbury, NY 11290</div>
  <div class="line"><svg width="11" height="11" style="color:var(--gold)"><use href="#cal"/></svg>September 20, 2015</div>
  <div class="line"><svg width="11" height="11" style="color:var(--gold)"><use href="#clock"/></svg>8 PM - 11PM</div>
</div>
<div class="abs event photo" style="left:900px;top:1512px;background:linear-gradient(135deg,#f4f3f0,#dcd8d0 60%,#a79d8e)" role="img" aria-label="Photo: white room with round table and carved chairs"></div>

<div class="abs event photo" style="left:0;top:1720px;background:linear-gradient(180deg,#d8c7a8,#b98a3c 55%,#7a4b1c)" role="img" aria-label="Photo: gilded ballroom with chandeliers"></div>
<div class="abs event event-text featured" style="left:300px;top:1720px">
  <h4>Bachelor Party</h4>
  <div class="line"><svg width="11" height="13" style="color:#fff"><use href="#pin"/></svg>St Aldwyn Chapel</div>
  <div class="line">41-43 Harlow Row Fenbury, NY 11290</div>
  <div class="line"><svg width="11" height="11" style="color:#fff"><use href="#cal"/></svg>September 20, 2015</div>
  <div class="line"><svg width="11" height="11" style="color:#fff"><use href="#clock"/></svg>8 PM - 11PM</div>
</div>
<div class="abs event photo" style="left:600px;top:1720px;background:linear-gradient(160deg,#f1d9a6,#b9864a 55%,#5e3d22)" role="img" aria-label="Photo: warm conference room with long table"></div>
<div class="abs event event-text" style="left:900px;top:1720px">
  <h4>Wedding Party</h4>
  <div class="line"><svg width="11" height="13" style="color:var(--gold)"><use href="#pin"/></svg>St Aldwyn Chapel</div>
  <div class="line">41-43 Harlow Row Fenbury, NY 11290</div>
  <div class="line"><svg width="11" height="11" style="color:var(--gold)"><use href="#cal"/></svg>September 20, 2015</div>
  <div class="line"><svg width="11" height="11" style="color:var(--gold)"><use href="#clock"/></svg>8 PM - 11PM</div>
</div>

<h2 class="abs section-heading script" style="top:1960px">Our Gallery</h2>
<div class="abs heading-rule" style="top:2022px"></div>

<div class="abs gallery-item" style="left:99px;top:2056px;width:228px;height:263px;background:linear-gradient(180deg,#3f4a63,#9aa0a8 60%,#c8b8a2)" role="img" aria-label="Photo: couple walking on a boardwalk"></div>
<div class="abs gallery-item" style="left:99px;top:2337px;width:228px;height:207px;background:linear-gradient(180deg,#7d8a70,#e8e8e6 50%,#9a9e8c)" role="img" aria-label="Photo: white wedding carriage"></div>
<div class="abs gallery-item" style="left:340px;top:2056px;width:228px;height:283px;background:linear-gradient(180deg,#c79a3c,#e3d2a6 55%,#4aa3a0)" role="img" aria-label="Photo: gold banquet hall with teal table settings"></div>
<div class="abs gallery-item" style="left:340px;top:2356px;width:228px;height:188px;background:linear-gradient(135deg,#efe6dc,#c9a98a 55%,#c23a3a)" role="img" aria-label="Photo: couple exchanging a gift"></div>
<div class="abs gallery-item" style="left:581px;top:2056px;width:281px;height:174px;background:linear-gradient(135deg,#e6dac0,#b7a68a 50%,#5c5652)" role="img" aria-label="Photo: wedding guests celebrating outdoors"></div>
<div class="abs gallery-item" style="left:581px;top:2247px;width:281px;height:297px;background:linear-gradient(180deg,#c9c1b2,#e7cfa0 45%,#a8442a 85%)" role="img" aria-label="Photo: catered buffet with canapés and drinks"></div>
<div class="abs gallery-item" style="left:876px;top:2056px;width:225px;height:224px;background:linear-gradient(180deg,#9b9287,#eeeeea 55%,#cfcfcc)" role="img" aria-label="Photo: white banquet tables with tall centrepieces"></div>
<div class="abs gallery-item" style="left:876px;top:2296px;width:225px;height:248px;background:linear-gradient(180deg,#d9b9a0,#b56d45 55%,#6d3b22)" role="img" aria-label="Photo: restaurant dining room with floral arrangements"></div>

<footer class="abs site-footer"></footer>

<div class="abs quote-box">
  <div class="abs avatar" role="img" aria-label="Client portrait"></div>
  <p class="abs quote-text">Etiam feugiat libero et sapien. Donec rutrum neque ac congue venenatis lorem ipsum pulvinar leo sollicitudin metus massa non velit. Maecenas elementum. In a nulla.</p>
  <div class="abs quote-nav">‹ ›</div>
  <div class="abs quote-name">- Clara Venn</div>
</div>

<div class="abs" style="left:93px;top:2730px;width:200px">
  <h3 class="footer-heading script">Get in Touch</h3>
  <div class="footer-rule"></div>
  <div class="social" style="margin-top:30px;justify-content:center;gap:18px" aria-label="Social links"><span aria-label="Pagewall"></span><span aria-label="Quillet"></span><span aria-label="Boardlyne"></span><span aria-label="Snapvuely"></span></div>
</div>

<div class="abs footer-brand"><div class="brand-mark"></div><div class="brand-name" style="font-size:22px">Elise Marlow</div></div>

<div class="abs" style="left:860px;top:2730px;width:240px">
  <h3 class="footer-heading script">Contact Us</h3>
  <div class="footer-rule"></div>
  <p class="footer-contact" style="margin-top:30px">info@elisemarlow.com<br>www.weddingsbyelisemarlow.<br>com</p>
</div>

<div class="abs bottom-bar">All right reserved. @2015 Copyright by Elise Marlow</div>

</body>
</html>
```